Oversized Postcard for Estate Planning & Probate 1st 2nd and 3rd prizes

Create a professional, fresh and polished oversized post card for law firm specializing in Estate Planning & Probate Law for High Net Worth Clients

Use any picture(s) of your choice (mine or ones you recommend), logo, headshot and company info

www.morvenashbylaw.com

Westbrook Office - 4800 Kestrel Avenue, Suite 900, Charlotte, NC 28210
Harlowe Office - 13470 Birch Court, Suite 400, Charlotte, NC 28277

Phone (704) 555-0187

Use this card for a Free Consultation

Target Market(s)

young and old families too; business owners

Industry/Entity Type

Law Firm

Font styles to use
Serif
Sans Serif

Requirements
Must have
• Use any picture(s) of your choice (mine or ones you recommend), logo, headshot and company info
• www.morvenashbylaw.com
• Westbrook Office - 4800 Kestrel Avenue, Suite 900, Charlotte, NC 28210
• Harlowe Office - 13470 Birch Court, Suite 400, Charlotte, NC 28277
• Phone (704) 555-0187
• Use this card for a Free Consultation
Nice to have
• great colors and great design; like graphics with depth /shading
Should not have
• don't use too many pics - keep it simple

```html
<!DOCTYPE html>
<html lang="en">
<head>
<meta charset="utf-8">
<title>Morven Ashby Law – Oversized Postcard</title>
<link rel="stylesheet" href="https://fonts.googleapis.com/css2?family=Arvo:wght@400;700&family=Open+Sans:ital,wght@0,300;0,400;0,600;0,700;1,600&display=swap">
<style>
:root{
  --page-bg:#3b3b3c;
  --card-bg:#ffffff;
  --brand-blue:#2a7fa6;
  --brand-blue-light:#3592bb;
  --brand-deep:#0f4e6c;
  --brand-mid:#1a6d93;
  --swoosh-grey:#5c6166;
  --line:#c9d6de;
  --mail-panel:#e6ecf3;
  --ink:#111111;
}
*{margin:0;padding:0;box-sizing:border-box}
html,body{width:904px;height:1200px;overflow:hidden;background:var(--page-bg)}
body{position:relative;font-family:"Open Sans",Arial,sans-serif}
.card{position:absolute;background:var(--card-bg);overflow:hidden;box-shadow:4px 6px 10px rgba(0,0,0,.45)}
.card--front{left:48px;top:60px;width:812px;height:524px;background:linear-gradient(90deg,#eef3f7 0%,#ffffff 60%)}
.card--back{left:48px;top:624px;width:810px;height:526px}
.abs{position:absolute}

/* front */
.front-art{left:0;top:0;width:812px;height:524px}
.headline{left:330px;top:30px;width:450px;text-align:right;font-family:"Arvo",Georgia,serif;font-weight:700;font-size:22px;line-height:28px;color:var(--brand-blue);text-shadow:1px 1px 1px rgba(0,0,0,.15)}
.brand-seal{left:364px;top:118px;width:184px;height:184px;border-radius:50%;background:#fff;box-shadow:0 3px 8px rgba(0,0,0,.25),inset 0 -4px 8px rgba(0,0,0,.06);display:flex;flex-direction:column;align-items:center;justify-content:center;text-align:center}
.brand-seal__name{font-weight:400;font-size:19px;color:var(--brand-blue);line-height:24px}
.brand-seal__sub{font-weight:400;font-size:9px;letter-spacing:1px;color:var(--brand-blue);margin-top:4px;border-top:1px solid var(--brand-blue);padding-top:4px;width:130px}
.intro{left:588px;top:106px;width:200px;text-align:center;font-weight:300;font-size:10.4px;line-height:16.8px;color:var(--brand-blue)}
.services{left:457px;top:306px;width:130px;list-style:none;text-align:center;font-family:"Arvo",Georgia,serif;font-size:13.5px;color:var(--brand-blue)}
.services li{height:21.2px;line-height:20px;border-bottom:1px solid var(--line);white-space:nowrap}
.services li:first-child{margin-left:-12px;margin-right:-12px;border-bottom-color:transparent}
.services li:last-child{border-bottom:none}
.headshot{left:607px;top:265px;width:172px;height:203px;border-radius:3px 3px 0 0;background:linear-gradient(160deg,#c9c1b4 0%,#9c948a 55%,#2a2a2d 100%)}
.front-band{left:0;top:468px;width:812px;height:56px}
.band-offer{left:30px;top:478px;font-size:13px;line-height:17px;color:#e5f1f7;font-weight:300}
.band-offer em{font-style:italic;font-weight:600;color:#fff}
.band-phone{left:200px;top:481px;font-size:16px;color:#fff;font-weight:400;white-space:nowrap}
.band-phone strong{font-size:21px;font-weight:700;letter-spacing:.5px}
.band-web{left:487px;top:480px;font-family:"Arvo",Georgia,serif;font-weight:700;font-size:21px;color:#fff;letter-spacing:.5px;white-space:nowrap}

/* back */
.top-band{left:0;top:0;width:642px;height:28px;background:linear-gradient(90deg,#1b7ea6,#0f4d6c)}
.office{top:28px;height:72px;background:linear-gradient(180deg,#1a6e95,#15648a);border-radius:0 0 6px 6px;color:#fff;padding:8px 12px}
.office--west{left:26px;width:200px;padding-left:14px}
.office--harlowe{left:230px;width:176px;padding-left:10px;padding-right:6px}
.office h2{font-size:14.5px;font-weight:600;line-height:20px;margin-bottom:6px;white-space:nowrap}
.office p{font-size:11px;line-height:16px;white-space:nowrap}
.office--harlowe p{font-size:10.6px}
.contact-mail{left:414px;top:44px;font-family:"Arvo",Georgia,serif;font-size:13px;letter-spacing:1.2px;color:var(--brand-blue);white-space:nowrap}
.contact-web{left:411px;top:70px;font-family:"Arvo",Georgia,serif;font-weight:700;font-size:16px;letter-spacing:.6px;color:var(--brand-blue);white-space:nowrap}
.postage{left:679px;top:14px;width:118px;height:117px;background:var(--mail-panel);display:flex;align-items:center;justify-content:center;text-align:center;font-family:Arial,Helvetica,sans-serif;font-size:15px;line-height:18px;color:var(--ink)}
.big-phone{left:80px;top:108px;font-family:"Arvo",Georgia,serif;font-weight:400;font-size:31px;color:var(--brand-blue);letter-spacing:.5px;white-space:nowrap}
.scene-photo{left:0;top:138px;width:540px;height:388px;background:linear-gradient(100deg,#ece9e3 0%,#e4ddd2 30%,#d6cfc5 55%,rgba(255,255,255,0) 100%)}
.brand-dot{left:420px;top:118px;width:92px;height:92px;border-radius:50%;background:radial-gradient(circle at 40% 35%,#2a8ab3,#0f4e6c 80%);box-shadow:0 0 0 2px #fff,0 0 0 4px #2b2b2b;display:flex;align-items:center;justify-content:center;text-align:center;font-size:12px;line-height:15px;color:#fff;font-weight:400}
.tagline{left:406px;top:234px;width:120px;text-align:center;list-style:none;font-weight:300;font-size:21.5px;letter-spacing:1.5px;color:var(--brand-blue-light);line-height:32.7px}
.address-area{left:540px;top:230px;width:257px;height:280px;background:var(--mail-panel)}
.barcode-area{left:361px;top:454px;width:436px;height:56px;background:var(--mail-panel)}
.mail-label{font-family:Arial,Helvetica,sans-serif;font-size:15px;color:var(--ink)}
.address-label{left:540px;top:276px;width:257px;text-align:center}
.barcode-label{left:361px;top:476px;width:436px;text-align:center;padding-right:8px}
.back-tag{left:0;top:469px;width:190px;height:57px}
.back-offer{left:28px;top:477px;font-size:13px;line-height:17px;color:#e5f1f7;font-weight:300}
.back-offer em{font-style:italic;font-weight:600;color:#fff}
</style>
</head>
<body>

<section class="card card--front" aria-label="Postcard front">
  <svg class="abs front-art" viewBox="0 0 812 524" aria-hidden="true">
    <defs>
      <linearGradient id="swooshBlue" x1="0" y1="0" x2="0" y2="1">
        <stop offset="0" stop-color="#1f7ea6"/><stop offset="1" stop-color="#0f4e6c"/>
      </linearGradient>
    </defs>
    <path d="M254 0 C330 30 400 120 396 220 C392 320 398 420 404 468" fill="none" stroke="var(--swoosh-grey)" stroke-width="9"/>
    <path d="M280 0 C350 40 416 130 410 230 C404 330 406 420 412 468" fill="none" stroke="url(#swooshBlue)" stroke-width="14"/>
  </svg>
  <svg class="abs" style="left:0;top:0" width="404" height="468" role="img" aria-label="Photo: smiling senior couple on a bicycle in a sunny park">
    <defs>
      <linearGradient id="parkTones" x1="0" y1="0" x2="0" y2="1">
        <stop offset="0" stop-color="#e2ead8"/><stop offset=".45" stop-color="#b7cd8e"/><stop offset="1" stop-color="#8fb061"/>
      </linearGradient>
    </defs>
    <path d="M0 0 H250 C325 30 392 120 388 220 C384 320 390 420 396 468 H0Z" fill="url(#parkTones)"/>
  </svg>

  <h1 class="abs headline">Serving clients with compassion and legal guidance is our passion...</h1>

  <div class="abs brand-seal">
    <span class="brand-seal__name">Morven Ashby</span>
    <span class="brand-seal__sub">LAW PLLC</span>
  </div>

  <p class="abs intro">Morven Ashby Law, PLLC serving clients in estate planning, estate administration, probate law, wills, revocable trusts, irrevocable trusts, powers of attorney, health care powers of attorney, living wills, hipaa releases, guardianships, special needs planning, wealth transfers, elder law and business law in North Carolina and South Carolina.</p>

  <ul class="abs services">
    <li>Estate Administration</li>
    <li>Probate Law</li>
    <li>Estate Planning</li>
    <li>Wills</li>
    <li>Trusts</li>
    <li>Living Wills</li>
    <li>Healthcare Powers</li>
  </ul>

  <div class="abs headshot" role="img" aria-label="Portrait photo of attorney Morven Ashby"></div>

  <svg class="abs front-band" viewBox="0 0 812 56" aria-hidden="true">
    <rect width="812" height="56" fill="#0f4e6c"/>
    <polygon points="0,0 208,0 156,56 0,56" fill="#1a6f96"/>
    <polygon points="208,0 430,0 378,56 156,56" fill="#1f7ba3"/>
    <polygon points="430,0 812,0 812,56 378,56" fill="#104f6e"/>
  </svg>
  <p class="abs band-offer">Use this card for a<br><em>Free Consultation</em></p>
  <p class="abs band-phone">Phone: <strong>(704) 555-0187</strong></p>
  <p class="abs band-web">www.morvenashbylaw.com</p>
</section>

<section class="card card--back" aria-label="Postcard back">
  <div class="abs scene-photo" role="img" aria-label="Photo: toddler in an aviator cap holding a toy plane in a bright playroom"></div>
  <div class="abs top-band"></div>
  <div class="abs office office--west">
    <h2>Westbrook Office</h2>
    <p>4800 Kestrel Avenue, Suite 900,<br>Charlotte, NC 28210</p>
  </div>
  <div class="abs office office--harlowe">
    <h2>Harlowe Office</h2>
    <p>13470 Birch Court, Suite 400,<br>Charlotte, NC 28277</p>
  </div>
  <p class="abs contact-mail">morven@morvenashbylaw.com</p>
  <p class="abs contact-web">www.morvenashbylaw.com</p>
  <div class="abs postage">Postage<br>Area</div>

  <p class="abs big-phone">(704) 555-0187</p>

  <div class="abs brand-dot">Morven<br>Ashby</div>

  <ul class="abs tagline">
    <li>big</li><li>things</li><li>start</li><li>from</li><li>little</li><li>ideas</li>
  </ul>

  <div class="abs address-area"></div>
  <div class="abs barcode-area"></div>
  <p class="abs mail-label address-label">Address Area</p>
  <p class="abs mail-label barcode-label">Barcode Area</p>

  <svg class="abs back-tag" viewBox="0 0 190 57" aria-hidden="true">
    <polygon points="0,0 178,0 140,57 0,57" fill="#1a6f96"/>
  </svg>
  <p class="abs back-offer">Use this card for a<br><em>Free Consultation</em></p>
</section>

</body>
</html>
```